Web Design Project - brivolta

I'm building an agency for marketing solutions but also medical education and patients education for pharmaceutical companies, medical societies and patient advocacy groups. We want to be perceived as the most innovative in the market. We work through design thinking solutions for campaigns and services.
I love some websites based on Swiss style design like www.quorlinex.com
We are a small group of designers, physicians and creatives working together to deliver the best experiences in our market.
We decided to also use pixel bazaar expecting that we maybe found a great idea we didn't thought about yet.

I'm extending it for more 2 weeks

Reason: I need the best design you can. Only PSD. No code needed. Love Swiss style, like velmora 5 and quorlinex.com I'm extending the deadline until get something great. Willing to extend as much as needed.

Target Market(s)

Pharmaceutical companies, physicians, medical societies, patients advocacy groups

Industry/Entity Type

Pharmaceutical

Font styles to use
Other font styles liked:
• Helvetia family

Colors

Designer to choose colors to be used in the design.

Requirements
Must have
• Must be innovative like www.quorlinex.com
Nice to have
• Cool menus
Should not have
• Not to appear too much Comercial. We like to be a boutique in this market. Craftsmen working with less clients at time but delivering precious stones.

```html
<!DOCTYPE html>
<html lang="en">
<head>
<meta charset="utf-8">
<title>Brivolta</title>
<link href="https://fonts.googleapis.com/css2?family=Roboto+Condensed:wght@400;700&family=Roboto:wght@300;400&display=swap" rel="stylesheet">
<style>
:root{
  --orange:#f7941d;
  --coral:#f4513a;
  --white:#ffffff;
  --text-soft:rgba(255,255,255,0.88);
  --tile-top:rgba(58,44,78,0.86);
  --tile-bottom:rgba(40,32,62,0.9);
  --divider:rgba(255,255,255,0.45);
}
*{margin:0;padding:0;box-sizing:border-box}
html,body{width:1200px;height:1142px;overflow:hidden}
body{
  position:relative;
  font-family:'Roboto',sans-serif;
  color:var(--white);
  background:
    radial-gradient(ellipse 380px 260px at 560px 260px, rgba(215,170,230,0.75), transparent 70%),
    radial-gradient(ellipse 300px 240px at 720px 560px, rgba(190,150,235,0.6), transparent 70%),
    radial-gradient(ellipse 320px 320px at 60px 140px, rgba(150,60,150,0.8), transparent 70%),
    radial-gradient(ellipse 300px 400px at 1180px 200px, rgba(90,130,210,0.8), transparent 70%),
    radial-gradient(ellipse 300px 300px at 1150px 1050px, rgba(140,110,80,0.6), transparent 70%),
    radial-gradient(ellipse 360px 300px at 120px 900px, rgba(110,70,200,0.8), transparent 70%),
    linear-gradient(135deg,#4a3a9e 0%,#6a4fb8 40%,#5a48b0 70%,#4a3f96 100%);
}
.abs{position:absolute}
.cond{font-family:'Roboto Condensed',sans-serif}

.logo{left:153px;top:0;width:155px;height:100px;background:var(--orange);
  display:flex;align-items:center;justify-content:center;
  font-family:'Roboto Condensed',sans-serif;font-weight:700;font-size:32px;letter-spacing:0.5px}

.main-nav{left:0;top:42px;height:35px;display:flex}
.main-nav a{position:absolute;top:0;height:35px;line-height:35px;color:var(--white);
  text-decoration:none;font-family:'Roboto Condensed',sans-serif;font-size:15px;white-space:nowrap}
.main-nav .sep{position:absolute;top:0;width:1px;height:35px;background:var(--divider)}

.welcome{right:458px;top:162px;width:560px;text-align:right}
.welcome h1{font-family:'Roboto Condensed',sans-serif;font-weight:700;font-size:17px;line-height:22px;margin-bottom:5px}
.welcome p{font-size:13px;line-height:20.5px;font-weight:400;color:var(--text-soft)}

.about-tile{left:773px;top:149px;width:275px;height:137px;display:flex}
.about-tile .label{width:137px;height:137px;background:var(--coral);display:flex;flex-direction:column;
  align-items:center;justify-content:center;font-family:'Roboto Condensed',sans-serif;font-weight:700;font-size:17px}
.about-tile .label svg{margin-bottom:14px}

.photo{background:linear-gradient(135deg,#cfc9c4,#8f8a92)}
.photo.warm{background:linear-gradient(135deg,#e8ddd6,#b98e9e 60%,#8c4a7a)}
.photo.grey{background:linear-gradient(135deg,#e2e2e2,#8a8a8a)}
.photo.crowd{background:linear-gradient(135deg,#9b8574,#5d4a3e 55%,#2e2620)}
.photo.doctor{background:linear-gradient(135deg,#dfe3e8,#f2f2f2 50%,#b7c1c9)}

.tile{background:linear-gradient(180deg,var(--tile-top),var(--tile-bottom));padding:24px 24px}
.tile h2{font-family:'Roboto Condensed',sans-serif;font-weight:400;font-size:20px;line-height:23px;text-transform:uppercase;margin-bottom:14px}
.tile p{font-weight:300;font-size:14px;line-height:22px;color:var(--text-soft)}

.contact-card{left:837px;top:547px;width:211px;height:281px}
.contact-card .text{position:absolute;left:0;top:177px;width:211px;height:104px;
  background:linear-gradient(180deg,var(--tile-top),var(--tile-bottom));padding:14px 23px}
.contact-card h2{font-family:'Roboto Condensed',sans-serif;font-weight:400;font-size:20px;line-height:24px;margin-bottom:6px}
.contact-card p{font-weight:300;font-size:14px;line-height:22px;color:var(--text-soft)}

.advocacy{left:611px;top:843px;width:438px;height:194px}
.advocacy .bar{position:absolute;left:0;bottom:0;width:100%;height:58px;
  background:linear-gradient(180deg,rgba(20,15,25,0.1),rgba(20,15,25,0.7));display:flex;align-items:center;padding:0 24px}
.advocacy h2{font-family:'Roboto Condensed',sans-serif;font-weight:400;font-size:17px;width:218px}
.advocacy p{font-weight:300;font-size:13.5px;line-height:17px;color:var(--text-soft)}

.follow{left:155px;top:1063px;font-family:'Roboto Condensed',sans-serif;font-size:14px}
.social{left:157px;top:1087px;display:flex;gap:6px}
.social span{width:30px;height:30px;border:1.5px solid var(--white);border-radius:50%;display:block}
.social span+span{margin-left:0}

.footer-nav{right:149px;top:1063px;display:flex;gap:10px;font-family:'Roboto Condensed',sans-serif;font-size:14px}
.footer-nav a{color:var(--white);text-decoration:none}
.copyright{right:149px;top:1091px;font-family:'Roboto Condensed',sans-serif;font-size:14px}
</style>
</head>
<body>

<div class="abs logo">BRIVOLTA</div>

<nav class="abs main-nav">
  <a style="left:605px">HOME</a>
  <span class="sep" style="left:661px"></span>
  <a style="left:682px">ABOUT US</a>
  <span class="sep" style="left:762px"></span>
  <a style="left:785px">SERVICES</a>
  <span class="sep" style="left:863px"></span>
  <a style="left:882px">PRODUCTS</a>
  <span class="sep" style="left:967px"></span>
  <a style="left:990px">CONTACT</a>
</nav>

<section class="abs welcome">
  <h1>WELOCME TO BRIVOLTA</h1>
  <p>Lorem Ipsum is simply dummy text of the printing and typesetting industry. Lorem<br>
  Ipsum has been the industry's standard dummy text ever since the 1500s, when an<br>
  unknown printer took a galley of type and scrambled it to make a type specimen book.<br>
  It has survived not only five centuries,</p>
</section>

<div class="abs about-tile">
  <div class="label">
    <svg width="40" height="52" viewBox="0 0 40 52" aria-hidden="true">
      <circle cx="20" cy="12" r="11" fill="#fff"/>
      <path d="M0 52 V40 Q0 28 12 28 H28 Q40 28 40 40 V52 Z" fill="#fff"/>
    </svg>
    ABOUT US
  </div>
  <div class="photo doctor" style="width:138px;height:137px" role="img" aria-label="Photo of a smiling doctor and nurse"></div>
</div>

<div class="abs photo grey" style="left:153px;top:312px;width:211px;height:222px" role="img" aria-label="Photo of a person typing on a laptop"></div>
<article class="abs tile" style="left:380px;top:312px;width:211px;height:222px">
  <h2>Marketing<br>Solutions</h2>
  <p>Contrary to popular belief, Lorem Ipsum is not simply random text has roots in a piece of classical.</p>
</article>
<article class="abs tile" style="left:611px;top:312px;width:211px;height:222px">
  <h2>Medical<br>Education</h2>
  <p>Contrary to popular belief, Lorem Ipsum is not simply random text has roots in a piece of classical.</p>
</article>
<div class="abs photo doctor" style="left:836px;top:312px;width:211px;height:222px" role="img" aria-label="Photo of a doctor with a stethoscope and laptop"></div>

<div class="abs photo warm" style="left:153px;top:547px;width:437px;height:281px" role="img" aria-label="Photo of a pharmacist showing a leaflet to a patient"></div>
<article class="abs tile" style="left:609px;top:547px;width:213px;height:281px">
  <h2>Patients<br>Education</h2>
  <p>The standard chunk of Lorem Ipsum used since the 1500s is reproduced below for those inter-ested. Sections 1.10.32 and 1.10.33 from "de Finibus Bonorum.</p>
</article>
<article class="abs contact-card">
  <div class="photo grey" style="width:211px;height:177px" role="img" aria-label="Black and white photo of a woman on the telephone"></div>
  <div class="text">
    <h2>CONTACT US</h2>
    <p>The standard chunk of Lorem Ipsum used since .</p>
  </div>
</article>

<div class="abs photo grey" style="left:154px;top:843px;width:193px;height:194px" role="img" aria-label="Photo of hands holding a tablet with an anatomy chart"></div>
<article class="abs tile" style="left:355px;top:843px;width:236px;height:194px;padding-top:18px">
  <h2 style="margin-bottom:6px">Medical<br>Societies</h2>
  <p>The standard chunk of Lorem Ipsum used since the 1500s is reproduced below for those interested.</p>
</article>
<article class="abs advocacy">
  <div class="photo crowd" style="width:100%;height:100%" role="img" aria-label="Photo of a cheering crowd of people"></div>
  <div class="bar">
    <h2>PATIENT ADVOCACY GROUPS</h2>
    <p>The standard chunk of<br>Lorem Ipsum used intersted.</p>
  </div>
</article>

<div class="abs follow">FOLLOW</div>
<div class="abs social" aria-label="Social links">
  <span></span><span></span><span></span><span></span>
</div>

<nav class="abs footer-nav">
  <a>HOME</a><a>ABOUT US</a><a>SERVICES</a><a>PRODUCTS</a><a>CONTACT US</a>
</nav>
<div class="abs copyright">COPYRIGHTS @ 2014 ALL RIGHTS RESERVED</div>

</body>
</html>
```